Harborline Renewal Business Card Design

Professional and clean design. The design colors should flow with the logo. Two-sided card with the website on the back which is:

www.HarborlineRenewal.example.

"Specializing in Water Damage Restoration"

On the front I need the name, email, phone, and logo.

Name: Darnell Quisby
Email: Darnell@HarborlineRenewal.example
Phone: 555-318-2046 for now

I only have the Preview and Thumbnail right now but should have the source files uploaded within a day or two.

Target Market(s)

Flood victims, home owners with water damage from busted pipes etc...

Industry/Entity Type

Business

Contact Information for Business Card

Name: Darnell Quisby

Font styles to use
Serif
Sans Serif

Requirements
Must have
• Business Card Details Info

```html
<!DOCTYPE html>
<html lang="en">
<head>
<meta charset="utf-8">
<title>Harborline Renewal – Business Card</title>
<link rel="stylesheet" href="https://fonts.googleapis.com/css2?family=Cinzel:wght@400;600;700&family=Open+Sans:wght@400&display=swap">
<style>
  :root {
    --backdrop: #ece9e4;
    --card-white: #ffffff;
    --sky: #5bbfee;
    --ocean: #2e8fd0;
    --brand-blue: #2f9ad6;
    --navy: #1d2a38;
    --ink: #1a1a1a;
    --text: #222a30;
    --divider: #9aa3aa;
  }
  html, body {
    margin: 0;
    padding: 0;
    width: 1200px;
    height: 1036px;
    overflow: hidden;
    background: var(--backdrop);
  }
  .canvas {
    position: relative;
    width: 1200px;
    height: 1036px;
  }
  .card {
    position: absolute;
    width: 795px;
    height: 452px;
    border-radius: 34px;
    overflow: hidden;
    box-shadow: 0 2px 6px rgba(0,0,0,0.18);
  }
  .card--front {
    left: 360px;
    top: 39px;
    background: var(--card-white);
  }
  .card--back {
    left: 39px;
    top: 545px;
    background: var(--sky);
  }
  .front-swoosh {
    position: absolute;
    inset: 0;
    width: 100%;
    height: 100%;
  }
  .holder {
    position: absolute;
    right: 36px;
    top: 26px;
    text-align: right;
    font-family: "Cinzel", serif;
    color: var(--navy);
  }
  .holder__name {
    font-size: 25px;
    font-weight: 600;
    letter-spacing: 1px;
    line-height: 1.2;
  }
  .holder__title {
    font-size: 21px;
    font-weight: 400;
    letter-spacing: 1.5px;
    line-height: 1.3;
  }
  .brand {
    position: absolute;
    left: 36px;
    top: 108px;
    width: 312px;
    text-align: center;
    font-family: "Cinzel", serif;
    font-weight: 600;
    color: var(--brand-blue);
  }
  .brand__dot {
    display: block;
    width: 88px;
    height: 88px;
    margin: 0 auto 14px;
    border-radius: 50%;
    background: var(--sky);
  }
  .brand__name {
    font-size: 40px;
    line-height: 1;
    letter-spacing: 1px;
  }
  .brand__sub {
    display: block;
    font-size: 19px;
    letter-spacing: 5px;
    margin-top: 6px;
  }
  .contact {
    position: absolute;
    left: 36px;
    top: 342px;
    font-family: "Open Sans", sans-serif;
    font-size: 19px;
    color: var(--text);
  }
  .contact__row {
    display: flex;
    align-items: center;
    height: 31px;
  }
  .contact__icon {
    width: 16px;
    height: 16px;
    margin-right: 9px;
    flex: none;
  }
  .address {
    position: absolute;
    left: 415px;
    top: 373px;
    padding-left: 16px;
    border-left: 1.5px solid var(--divider);
    font-family: "Open Sans", sans-serif;
    font-size: 19px;
    color: var(--text);
    line-height: 31px;
  }
  .back-mark {
    position: absolute;
    left: 266px;
    top: 48px;
    width: 262px;
    height: 262px;
    border-radius: 50%;
    border: 14px solid var(--ink);
    box-sizing: border-box;
    display: flex;
    align-items: center;
    justify-content: center;
    text-align: center;
    font-family: "Cinzel", serif;
    font-weight: 700;
    font-size: 28px;
    line-height: 1.15;
    color: var(--ink);
  }
  .tagline {
    position: absolute;
    left: 0;
    right: 0;
    top: 356px;
    text-align: center;
    font-family: "Cinzel", serif;
    font-size: 21px;
    letter-spacing: 1px;
    color: var(--navy);
  }
</style>
</head>
<body>
<main class="canvas">

  <section class="card card--front" aria-label="Business card front">
    <svg class="front-swoosh" viewBox="0 0 513 292" preserveAspectRatio="none" aria-hidden="true">
      <path d="M0,0 H513 V140 C380,40 180,20 0,66 Z" fill="var(--sky)"/>
      <path d="M0,82 C170,34 380,50 513,150 V164 C380,64 170,52 0,94 Z" fill="var(--ocean)"/>
    </svg>

    <div class="holder">
      <div class="holder__name">Darnell Quisby</div>
      <div class="holder__title">Title</div>
    </div>

    <div class="brand">
      <span class="brand__dot"></span>
      <div class="brand__name">Harborline</div>
      <span class="brand__sub">Renewal</span>
    </div>

    <div class="contact">
      <div class="contact__row">
        <svg class="contact__icon" viewBox="0 0 16 16" aria-hidden="true">
          <path d="M4 1.5 L6.2 4.5 L4.8 6 C5.6 8 7.8 10.3 10 11.2 L11.5 9.8 L14.5 12 L13 14.5 C7 14.5 1.5 9 1.5 3 Z" fill="none" stroke="var(--brand-blue)" stroke-width="1.5" stroke-linejoin="round"/>
        </svg>
        <span>555-318-2046</span>
      </div>
      <div class="contact__row">
        <svg class="contact__icon" viewBox="0 0 16 16" aria-hidden="true">
          <rect x="1.5" y="4" width="13" height="9" rx="1" fill="var(--brand-blue)"/>
          <path d="M1.8 4.4 L8 9 L14.2 4.4" fill="none" stroke="#fff" stroke-width="1.3"/>
        </svg>
        <span>Darnell@HarborlineRenewal.example</span>
      </div>
      <div class="contact__row">
        <svg class="contact__icon" viewBox="0 0 16 16" aria-hidden="true">
          <circle cx="8" cy="8" r="6.5" fill="none" stroke="var(--brand-blue)" stroke-width="1.4"/>
          <ellipse cx="8" cy="8" rx="2.8" ry="6.5" fill="none" stroke="var(--brand-blue)" stroke-width="1.2"/>
          <path d="M1.5 8 H14.5" stroke="var(--brand-blue)" stroke-width="1.2"/>
        </svg>
        <span>www.HarborlineRenewal.example</span>
      </div>
    </div>

    <div class="address">
      <div>Street Name, City Name</div>
      <div>Zipcode-12345</div>
    </div>
  </section>

  <section class="card card--back" aria-label="Business card back">
    <div class="back-mark">Harborline<br>Renewal</div>
    <p class="tagline">Specializing in Water Damage Restoration</p>
  </section>

</main>
</body>
</html>
```